Business cards for 3 Realtors at one brokerage

We will need a business card template that can be projected on 3 business cards. Harborline Property Group has 3 realtors on staff Dane, Owen, and Miles. We all want a business card that shows our new logo and information. I will attach many versions of our Logo as well as head shots for each realtor (Owen- Long hair, youngest. Miles- Suit jacket, parted hair cut. Dane- Angled Pose, Shirt and Tie.) I have attached our information below.

Dane Foskett
801-555-0147
dane@harborlinehomesite.com
Principal Broker

Miles Tandrow
801-555-0162
miles@harborlinehomesite.com
Real Estate Agent

Owen Tandrow
801-555-0138
owen@harborlinehomesite.com
Real Estate Agent

Harborline Property Group
HarborlineHomesite.com
5286 N 7200 Suite 208-617, Alder Creek, UT 84990

Please feel free to reach out with any questions, comments, or concerns.

```html
<!DOCTYPE html>
<html lang="en">
<head>
<meta charset="utf-8">
<title>Harborline Property Group – Business Card</title>
<link href="https://fonts.googleapis.com/css2?family=Montserrat:wght@600&family=Arimo:wght@400&display=swap" rel="stylesheet">
<style>
  :root {
    --brand-blue: #35a8f4;
    --ink: #333333;
    --logo-grey: #5a5a5a;
    --rule-grey: #6b6b6b;
    --paper: #ffffff;
    --backdrop: #2e2e2e;
    --photo-light: #ececec;
    --photo-dark: #c9c9c9;
  }
  * { margin: 0; padding: 0; box-sizing: border-box; }
  html, body { width: 1200px; height: 866px; overflow: hidden; }
  body {
    background: var(--backdrop);
    position: relative;
    font-family: "Arimo", Arial, sans-serif;
  }
  .card {
    position: absolute;
    left: 250px;
    width: 700px;
    height: 400px;
    overflow: hidden;
    box-shadow: 0 6px 18px rgba(0,0,0,.45);
  }
  .card--front { top: 18px; background: var(--paper); }
  .card--back { top: 448px; background: var(--brand-blue); }

  .card__art { position: absolute; inset: 0; }

  /* Brand mark */
  .brand {
    position: absolute;
    display: flex;
    flex-direction: column;
    align-items: center;
    text-align: center;
    font-family: "Montserrat", sans-serif;
    font-weight: 600;
    text-transform: uppercase;
  }
  .brand__circle { border-radius: 50%; border-style: solid; }
  .brand__name { line-height: 1.1; letter-spacing: 3px; }
  .brand__sub { letter-spacing: 4px; margin-top: 4px; }

  .card--front .brand { left: 30px; top: 26px; width: 300px; color: var(--logo-grey); }
  .card--front .brand__circle { width: 66px; height: 66px; border-width: 5px; border-color: var(--brand-blue); }
  .card--front .brand__name { margin-top: 12px; font-size: 24px; }
  .card--front .brand__sub { font-size: 10px; }

  .card--back .brand { left: 100px; top: 96px; width: 500px; color: var(--paper); }
  .card--back .brand__circle { width: 110px; height: 110px; border-width: 7px; border-color: var(--paper); }
  .card--back .brand__name { margin-top: 22px; font-size: 38px; }
  .card--back .brand__sub { font-size: 15px; margin-top: 8px; }

  /* Contact list */
  .contact {
    position: absolute;
    left: 40px;
    top: 180px;
    list-style: none;
    color: var(--ink);
    font-size: 16px;
    line-height: 1.3;
  }
  .contact__item { display: flex; align-items: flex-start; gap: 10px; margin-bottom: 8px; }
  .contact__icon { width: 20px; height: 20px; flex: none; }

  /* Agent */
  .headshot {
    position: absolute;
    left: 450px;
    top: 34px;
    width: 210px;
    height: 220px;
    border: 3px solid var(--brand-blue);
    background: linear-gradient(160deg, var(--photo-light), var(--photo-dark));
  }
  .agent {
    position: absolute;
    right: 40px;
    top: 266px;
    text-align: right;
  }
  .agent__name {
    font-family: "Montserrat", sans-serif;
    font-weight: 600;
    font-size: 22px;
    letter-spacing: 1px;
    text-transform: uppercase;
    color: var(--brand-blue);
  }
  .agent__title { font-size: 17px; color: var(--ink); margin-top: 2px; }

  .website {
    position: absolute;
    right: 40px;
    bottom: 18px;
    color: var(--paper);
    font-size: 17px;
    letter-spacing: .5px;
  }
</style>
</head>
<body>

  <section class="card card--front">
    <svg class="card__art" viewBox="0 0 700 400" aria-hidden="true">
      <path d="M0 343 L250 343" stroke="var(--rule-grey)" stroke-width="7"/>
      <path d="M0 352 L250 352 C290 352 300 330 345 330 L700 330 L700 400 L0 400 Z" fill="var(--brand-blue)"/>
    </svg>

    <div class="brand">
      <span class="brand__circle"></span>
      <span class="brand__name">Harborline</span>
      <span class="brand__sub">Property Group</span>
    </div>

    <ul class="contact">
      <li class="contact__item">
        <svg class="contact__icon" viewBox="0 0 20 20"><circle cx="10" cy="10" r="9" fill="none" stroke="var(--brand-blue)" stroke-width="2"/><path d="M10 5a3.2 3.2 0 0 0-3.2 3.2c0 2.4 3.2 6 3.2 6s3.2-3.6 3.2-6A3.2 3.2 0 0 0 10 5z" fill="var(--brand-blue)"/><circle cx="10" cy="8.2" r="1.2" fill="#fff"/></svg>
        <span>5286 N 7200 Suite 208-617<br>Alder Creek, UT 84990</span>
      </li>
      <li class="contact__item">
        <svg class="contact__icon" viewBox="0 0 20 20"><circle cx="10" cy="10" r="9" fill="none" stroke="var(--brand-blue)" stroke-width="2"/><path d="M7 5.5l2 2.2-1 1.3c.6 1.3 1.6 2.3 2.9 2.9l1.3-1 2.2 2-1.2 1.6C9.7 14.2 5.8 10.3 5.5 6.8z" fill="var(--brand-blue)"/></svg>
        <span>801-555-0138</span>
      </li>
      <li class="contact__item">
        <svg class="contact__icon" viewBox="0 0 20 20"><circle cx="10" cy="10" r="9" fill="none" stroke="var(--brand-blue)" stroke-width="2"/><rect x="5" y="6.5" width="10" height="7" fill="var(--brand-blue)"/><path d="M5 6.5l5 4 5-4" fill="none" stroke="#fff" stroke-width="1.2"/></svg>
        <span>owen@harborlinehomesite.com</span>
      </li>
    </ul>

    <div class="headshot" role="img" aria-label="Headshot of Owen Tandrow"></div>

    <div class="agent">
      <p class="agent__name">Owen Tandrow</p>
      <p class="agent__title">Real Estate Agent</p>
    </div>

    <p class="website">www.HarborlineHomesite.com</p>
  </section>

  <section class="card card--back">
    <div class="brand">
      <span class="brand__circle"></span>
      <span class="brand__name">Harborline</span>
      <span class="brand__sub">Property Group</span>
    </div>
  </section>

</body>
</html>
```